Federal IT Consulting Company - Brisolux Consulting Group

We're seeking a skilled web designer to create a modern, bold, and engaging WordPress website for Brisolux Consulting Group, LLC. Our company specializes in federal IT consulting, and our name is a play on "Brightening Solutions." The website should reflect our expertise in the federal technology marketplace and position us as a trusted partner for clients navigating their IT journey.

contact: info@brisoluxgrp-example.com

Current Status

WordPress is already installed on our hosting account
We have an existing logo (may need modernization)

Design Requirements

Style:

Modern and visually striking design
Bold elements to convey confidence and expertise
Incorporate the concept of "brightening solutions" into the design

Features:

Modern UX sliders for dynamic content presentation
Eye-catching, high-quality images (stock photos to be sourced by the designer)
Responsive design for all devices

Color Scheme:

To be proposed by the designer, should align with our brand and convey trust and technological expertise

Logo:

Evaluate our current logo
Create a transparent background version if needed
Propose modernization if deemed necessary

Accessibility:

Ensure design elements are accessible to users with disabilities
Use high contrast ratios for text and background colors
Provide text alternatives for non-text content

Website Structure
Create the following pages, with the possibility of subpages:

Home
Services
About
Contact

Specific Page Requirements
Home Page

Striking hero section with a clear value proposition
Overview of our services
Client testimonials or trust indicators

Services Page

Detailed list of our IT consulting services
Clear explanation of how we help navigate the federal IT landscape

About Page

Company history and mission
Team highlights (if applicable)
Our approach to federal IT consulting

Contact Page

Contact form
Other contact methods (phone, email)

Technical Requirements

Fully responsive design
SEO best practices implemented
Fast loading times
Integration with necessary plugins (to be discussed)
Training on how to update and maintain the site
Full compliance with Web Content Accessibility Guidelines (WCAG) 2.1 Level AA
Adherence to Section 508 standards for federal website accessibility
Implementation of necessary features for ADA compliance
Updates

Designs look the same

Target Market(s)

US Federal Govt customers looking for IT support.

Industry/Entity Type

IT Consulting

Coding

Coded - Design and coding required

Colors
0054AA
0677BA
7BADD7
CADEEF
E8F1F8
0094D4
00A9DD
6FCCEA
C7EBF8
E9F6FB
00AB8E
00BBA5
67D7C9
C6EFE9
E9F9F6

```html
<!DOCTYPE html>
<html lang="en">
<head>
<meta charset="utf-8">
<title>Brisolux Consulting Group</title>
<link href="https://fonts.googleapis.com/css2?family=Michroma&family=Chakra+Petch:wght@500;600&family=Roboto:wght@400;500&family=Open+Sans:wght@400;600&display=swap" rel="stylesheet">
<style>
:root{
  --blue:#00A9DD;
  --blue-deep:#0094D4;
  --navy:#0A2A52;
  --ink:#2b2b2b;
  --muted:#555;
  --pale:#E9F6FB;
  --footer:#111111;
  --white:#ffffff;
}
*{margin:0;padding:0;box-sizing:border-box}
html,body{width:1200px;height:3606px;overflow:hidden}
body{position:relative;background:var(--white);font-family:'Roboto',sans-serif;color:var(--ink)}
.abs{position:absolute}
.display{font-family:'Michroma',sans-serif;letter-spacing:1px}
.btn{position:absolute;display:flex;align-items:center;justify-content:center;background:var(--blue);color:var(--white);font-family:'Chakra Petch',sans-serif;font-weight:600;font-size:17px;border-radius:24px;box-shadow:0 3px 8px rgba(0,0,0,.18)}
.accent{color:var(--blue)}
.rule{position:absolute;height:3px;background:var(--blue)}

/* header */
.site-header{left:0;top:0;width:1200px;height:87px;background:var(--white)}
.brand{left:98px;top:18px;display:flex;align-items:center;gap:10px}
.brand-mark{width:46px;height:46px;border-radius:50%;background:var(--blue)}
.brand-name{font-family:'Michroma',sans-serif;font-size:30px;color:var(--navy)}
.nav a{position:absolute;top:30px;font-family:'Chakra Petch',sans-serif;font-weight:500;font-size:19px;color:#333;text-decoration:none}
.nav .current{color:var(--blue);text-decoration:underline;text-underline-offset:5px}

/* hero */
.hero{left:0;top:87px;width:1200px;height:599px;background:radial-gradient(circle at 57% 62%,#3d7fc4 0%,#0d3f7a 30%,#082a56 65%,#061b38 100%)}
.hero-title{left:0;width:1200px;top:82px;text-align:center;color:var(--white);font-size:43px}
.hero-sub{left:300px;width:600px;top:140px;text-align:center;color:var(--white);font-size:16px;line-height:28px}
.slide-arrow{position:absolute;top:282px;width:34px;height:34px;border:2px solid rgba(255,255,255,.8);border-radius:50%}

/* about */
.about-photo{left:166px;top:839px;width:346px;height:346px;border-radius:50%;background:linear-gradient(135deg,#c8ccd0,#6b7682 55%,#2e3a46)}
.section-title{font-size:27px;color:#333}
.body-copy{font-size:15.4px;line-height:29px;color:var(--muted)}

/* services */
.services{left:0;top:1333px;width:1200px;height:1117px;background:linear-gradient(180deg,#f3f5f8,#e9eef3)}
.svc-icon{position:absolute;width:84px;height:84px}
.svc-heading{font-size:19px;color:#222}
.svc-ring{position:absolute;border-radius:50%}

/* testimonials */
.card{left:231px;top:2653px;width:736px;height:374px;background:var(--white);box-shadow:0 4px 18px rgba(0,0,0,.09)}
.quote-title{left:231px;width:736px;top:2712px;text-align:center;font-family:'Open Sans',sans-serif;font-weight:600;font-size:19px;color:#222}
.quote-text{left:270px;width:658px;top:2750px;text-align:center;font-family:'Open Sans',sans-serif;font-size:14.5px;line-height:31px;color:#444}
.avatar{position:absolute;border-radius:50%;border:3px solid var(--white)}

/* footer */
.site-footer{left:0;top:3161px;width:1200px;height:445px;background:var(--footer);color:var(--white)}
.foot-h{position:absolute;top:64px;font-family:'Michroma',sans-serif;font-size:21px;color:var(--white)}
.quick a{position:absolute;left:98px;color:var(--white);text-decoration:none;font-size:15px;display:flex;align-items:center;gap:12px}
.social{position:absolute;top:248px;width:28px;height:28px;border-radius:50%;background:var(--blue)}
.vline{position:absolute;top:90px;height:238px;border-left:1px dashed #bbb}
.detail-label{position:absolute;left:400px;font-weight:500;font-size:16px}
.detail-value{position:absolute;left:400px;font-size:15px}
.detail-icon{position:absolute;left:356px;width:32px;height:32px;border-radius:50%;background:var(--blue);display:flex;align-items:center;justify-content:center}
.dots{position:absolute;left:356px;width:239px;border-top:1px dotted #bbb}
.field{position:absolute;left:715px;width:353px;height:39px;border:1px solid #ddd;background:var(--footer);color:var(--white);font-size:14px;padding:11px 12px}
.submit{position:absolute;left:715px;top:262px;width:353px;height:38px;background:var(--blue);display:flex;align-items:center;justify-content:center;font-family:'Michroma',sans-serif;font-size:13px}
.copyright{left:0;width:1200px;top:408px;text-align:center;font-size:15px}
</style>
</head>
<body>

<header class="abs site-header">
  <div class="abs brand"><span class="brand-mark"></span><span class="brand-name">BRISOLUX</span></div>
  <nav class="nav">
    <a class="current" style="left:643px" href="#">Home</a>
    <a style="left:745px" href="#">Services</a>
    <a style="left:871px" href="#">About</a>
  </nav>
  <div class="btn" style="left:963px;top:20px;width:137px;height:46px">Contact Us</div>
</header>

<section class="abs hero" role="img" aria-label="Robotic hand and human hand reaching toward a glowing point among circuit lines">
  <h1 class="abs display hero-title">WELCOME TO BRISOLUX</h1>
  <p class="abs hero-sub">Lorem ipsum dolor sit amet, consectetur adipiscing elit, sed do eiusmod tempor incididunt ut labore et dolore magna aliqua.</p>
  <div class="btn" style="left:532px;top:208px;width:136px;height:45px">Get Started</div>
  <span class="slide-arrow" style="left:29px"><svg width="30" height="30" viewBox="0 0 30 30"><path d="M17 9 L11 15 L17 21" fill="none" stroke="#fff" stroke-width="1.6"/></svg></span>
  <span class="slide-arrow" style="left:1136px"><svg width="30" height="30" viewBox="0 0 30 30"><path d="M13 9 L19 15 L13 21" fill="none" stroke="#fff" stroke-width="1.6"/></svg></span>
</section>

<!-- about -->
<svg class="abs" style="left:126px;top:798px" width="428" height="428" viewBox="0 0 428 428"><circle cx="214" cy="214" r="195" fill="none" stroke="var(--blue)" stroke-width="24"/></svg>
<div class="abs about-photo" role="img" aria-label="Two colleagues in business attire reviewing a tablet in an office"></div>
<h2 class="abs display section-title" style="left:632px;top:793px">ABOUT <span class="accent">US</span></h2>
<span class="rule" style="left:632px;top:839px;width:50px"></span>
<p class="abs body-copy" style="left:632px;top:855px;width:472px">Sed ut perspiciatis unde omnis iste natus error sit voluptatem accusantium doloremque laudantium, totam rem aperiam, eaque ipsa quae ab illo inventore veritatis et quasi architecto beatae vitae dicta sunt explicabo. Nemo enim ipsam voluptatem quia voluptas sit aspernatur aut odit aut fugit, sed quia consequuntur magni dolores eos qui ratione voluptatem sequi nesciunt. Neque porro quisquam est, qui dolorem ipsum quia dolor sit amet, consectetur, adipisci velit, sed quia non numquam eius modi tempora incidunt ut labore et dolore magnam aliquam quaerat voluptatem. Ut enim ad minima laboriosam, nisi ut aliquid ex ea commodi consequatur?</p>
<div class="btn" style="left:632px;top:1163px;width:136px;height:48px">Read More</div>

<!-- services -->
<section class="abs services">
  <h2 class="abs display section-title" style="left:0;width:1200px;text-align:center;top:83px">OUR <span class="accent">SERVICES</span></h2>
  <span class="rule" style="left:575px;top:129px;width:50px"></span>

  <svg class="svc-icon" style="left:98px;top:182px" viewBox="0 0 84 84"><circle cx="42" cy="42" r="34" fill="none" stroke="var(--blue)" stroke-width="7"/><rect x="30" y="30" width="24" height="24" rx="3" fill="none" stroke="#333" stroke-width="2"/><path d="M35 38h14M35 42h14M35 46h14" stroke="#333" stroke-width="1.6"/></svg>
  <h3 class="abs display svc-heading" style="left:98px;top:287px">IT CONSULTING SERVICES</h3>
  <p class="abs body-copy" style="left:98px;top:322px;width:450px;line-height:28.3px">Lorem ipsum dolor sit amet, consectetur adipiscing elit, sed do eiusmod tempor incididunt ut labore et dolore magna aliqua. Ut enim ad minim veniam, quis nostrud exercitation ullamco laboris nisi ut aliquip ex ea commodo consequat. Duis aute irure fugiat nulla pariatur.</p>
  <div class="btn" style="left:98px;top:482px;width:139px;height:47px">Read More</div>
  <div class="svc-ring" style="left:657px;top:154px;width:400px;height:400px;background:#cfe6ef"></div>
  <div class="svc-ring" role="img" aria-label="Two engineers with a laptop in a server room" style="left:675px;top:172px;width:364px;height:364px;background:linear-gradient(140deg,#3a5a78,#1d2f44 60%,#c9d3dc)"></div>

  <div class="svc-ring" style="left:122px;top:617px;width:400px;height:400px;background:#d2d4d6"></div>
  <div class="svc-ring" role="img" aria-label="Aerial view of a historic government building among trees" style="left:140px;top:635px;width:364px;height:364px;background:linear-gradient(180deg,#8c9aab,#4f6a4a 45%,#6e6a5c)"></div>
  <svg class="svc-icon" style="left:658px;top:635px" viewBox="0 0 84 84"><circle cx="42" cy="42" r="34" fill="none" stroke="var(--blue)" stroke-width="7"/><path d="M28 36h28l-14-9z M30 38v12M38 38v12M46 38v12M54 38v12M27 52h30" fill="none" stroke="#333" stroke-width="2"/></svg>
  <h3 class="abs display svc-heading" style="left:660px;top:741px">FEDERAL IT LANDSCAPE</h3>
  <p class="abs body-copy" style="left:660px;top:776px;width:450px;line-height:28.3px">Lorem ipsum dolor sit amet, consectetur adipiscing elit, sed do eiusmod tempor incididunt ut labore et dolore magna aliqua. Ut enim ad minim veniam, quis nostrud exercitation ullamco laboris nisi ut aliquip ex ea commodo consequat. Duis aute irure fugiat nulla pariatur.</p>
  <div class="btn" style="left:661px;top:937px;width:137px;height:46px">Read More</div>
</section>

<!-- testimonials -->
<h2 class="abs display section-title" style="left:0;width:1200px;text-align:center;top:2532px">CLIENT TESTIMONIALS</h2>
<span class="rule" style="left:575px;top:2578px;width:50px"></span>
<div class="abs card"></div>
<svg class="abs" style="left:564px;top:2628px" width="72" height="56" viewBox="0 0 72 56"><path d="M4 52V30C4 14 14 5 28 3v10c-7 2-11 7-11 14h11v25z M40 52V30C40 14 50 5 64 3v10c-7 2-11 7-11 14h11v25z" fill="var(--blue)"/></svg>
<p class="abs quote-title">"A perfect place to book pet friendly vacations!!"</p>
<p class="abs quote-text">Lorem ipsum dolor sit amet, consectetur adipiscing elit, sed do eiusmod tempor incididunt ut labore et dolore magna aliqua. Ut enim ad minim veniam, quis nostrud exercitation ullamco laboris nisi ut aliquip ex ea commodo consequat.</p>
<p class="abs" style="left:231px;width:736px;top:2870px;text-align:center;font-family:'Open Sans',sans-serif;font-size:17px;color:var(--blue)">Marla Quen</p>
<p class="abs" style="left:231px;width:736px;top:2903px;text-align:center;font-family:'Open Sans',sans-serif;font-size:14.5px;color:#333">An avid traveler and pet lover</p>
<svg class="abs" style="left:576px;top:2935px" width="48" height="10" viewBox="0 0 48 10"><circle cx="8" cy="5" r="3.5" fill="#6fb8e4"/><circle cx="24" cy="5" r="3.5" fill="#1f5fae"/><circle cx="40" cy="5" r="3.5" fill="#6fb8e4"/></svg>
<div class="avatar" role="img" aria-label="Client portrait" style="left:476px;top:2989px;width:62px;height:62px;background:#b7b2ad"></div>
<div class="avatar" role="img" aria-label="Client portrait" style="left:557px;top:2978px;width:84px;height:84px;background:#a47a5c"></div>
<div class="avatar" role="img" aria-label="Client portrait" style="left:661px;top:2989px;width:62px;height:62px;background:#d9cfc6"></div>
<svg class="abs" style="left:196px;top:2826px" width="66" height="30" viewBox="0 0 66 30"><path d="M66 15H3M16 2 3 15l13 13" fill="none" stroke="var(--blue)" stroke-width="2.5"/></svg>
<svg class="abs" style="left:938px;top:2826px" width="66" height="30" viewBox="0 0 66 30"><path d="M0 15h63M50 2l13 13-13 13" fill="none" stroke="var(--blue)" stroke-width="2.5"/></svg>

<!-- footer -->
<footer class="abs site-footer">
  <h4 class="foot-h" style="left:98px">Quick Links</h4>
  <nav class="quick">
    <a href="#" style="top:105px"><svg width="14" height="12" viewBox="0 0 14 12"><path d="M0 6h11M7 1l5 5-5 5" fill="none" stroke="#fff" stroke-width="2.4"/></svg>Home</a>
    <a href="#" style="top:136px"><svg width="14" height="12" viewBox="0 0 14 12"><path d="M0 6h11M7 1l5 5-5 5" fill="none" stroke="#fff" stroke-width="2.4"/></svg>Services</a>
    <a href="#" style="top:167px"><svg width="14" height="12" viewBox="0 0 14 12"><path d="M0 6h11M7 1l5 5-5 5" fill="none" stroke="#fff" stroke-width="2.4"/></svg>About</a>
    <a href="#" style="top:197px"><svg width="14" height="12" viewBox="0 0 14 12"><path d="M0 6h11M7 1l5 5-5 5" fill="none" stroke="#fff" stroke-width="2.4"/></svg>Contact</a>
  </nav>
  <span class="social" style="left:98px"></span>
  <span class="social" style="left:136px"></span>
  <span class="social" style="left:174px"></span>
  <span class="social" style="left:210px"></span>
  <span class="vline" style="left:301px"></span>

  <h4 class="foot-h" style="left:356px">Contact Details</h4>
  <span class="detail-icon" style="top:112px"><svg width="14" height="14" viewBox="0 0 24 24"><path d="M6.6 10.8a15 15 0 0 0 6.6 6.6l2.2-2.2a1 1 0 0 1 1-.25 11.4 11.4 0 0 0 3.6.57 1 1 0 0 1 1 1V20a1 1 0 0 1-1 1A17 17 0 0 1 3 4a1 1 0 0 1 1-1h3.5a1 1 0 0 1 1 1c0 1.25.2 2.45.57 3.6a1 1 0 0 1-.25 1z" fill="#fff"/></svg></span>
  <span class="detail-label" style="top:104px">Phone;</span>
  <span class="detail-value" style="top:136px">+1 555 010 0199</span>
  <span class="dots" style="top:170px"></span>
  <span class="detail-icon" style="top:194px"><svg width="14" height="14" viewBox="0 0 24 24"><rect x="2" y="5" width="20" height="14" rx="2" fill="#fff"/><path d="M3 6l9 7 9-7" fill="none" stroke="var(--blue)" stroke-width="2"/></svg></span>
  <span class="detail-label" style="top:186px">Email:</span>
  <span class="detail-value" style="top:217px">info@brisoluxgrp-example.com</span>
  <span class="dots" style="top:251px"></span>
  <span class="detail-icon" style="top:280px"><svg width="14" height="14" viewBox="0 0 24 24"><path d="M12 2a7 7 0 0 0-7 7c0 5 7 13 7 13s7-8 7-13a7 7 0 0 0-7-7zm0 9.5A2.5 2.5 0 1 1 12 6.5a2.5 2.5 0 0 1 0 5z" fill="#fff"/></svg></span>
  <span class="detail-label" style="top:278px">Address:</span>
  <span class="detail-value" style="top:310px">Company Name,United State.</span>
  <span class="vline" style="left:671px"></span>

  <h4 class="foot-h" style="left:715px">Contact Me</h4>
  <div class="field" style="top:102px">Name:</div>
  <div class="field" style="top:156px">Email:</div>
  <div class="field" style="top:209px">Address:</div>
  <div class="submit">Submit Now</div>

  <span class="abs" style="left:98px;top:388px;width:1002px;border-top:1px solid #ccc"></span>
  <p class="abs copyright">Copyrights@2024.Company Name.All Rights Reserved</p>
</footer>

</body>
</html>
```